Brellwick Partners, LLC Stationary

Brellwick Partners, LLC is a new financial planning and consulting company. We are looking for designs on business cards, letterhead, envelopes, and anything else that would be useful. Our preference for business card design is two sided. We are looking for a professional and clean look with incorporating the logo and patriotic feel. Thank you to all who participate and good luck!

```html
<!DOCTYPE html>
<html lang="en">
<head>
<meta charset="utf-8">
<title>Brellwick Partners, LLC — Business Card</title>
<link rel="stylesheet" href="https://fonts.googleapis.com/css2?family=Arimo:wght@400;700&display=swap">
<style>
  :root {
    --stage: #2e2f31;
    --paper: #ffffff;
    --paper-shade: #eceef0;
    --navy: #123d6b;
    --navy-deep: #0e3159;
    --red: #d1252c;
    --white: #ffffff;
    --grey-text: #6b6f75;
  }
  * { box-sizing: border-box; margin: 0; padding: 0; }
  html, body { width: 1200px; height: 950px; overflow: hidden; }
  body {
    background: var(--stage);
    font-family: "Arimo", Arial, sans-serif;
    position: relative;
  }
  .card {
    position: absolute;
    left: 220px;
    width: 760px;
    height: 434px;
    background: var(--paper);
    overflow: hidden;
    box-shadow: 0 10px 30px rgba(0,0,0,.45);
  }
  .card--back { top: 28px; background: linear-gradient(135deg, var(--paper) 55%, var(--paper-shade)); }
  .card--front { top: 488px; }

  /* Back side */
  .back-lockup {
    position: absolute; inset: 0;
    display: flex; flex-direction: column; align-items: center; justify-content: center;
    gap: 14px;
  }
  .back-name {
    display: flex; align-items: center; gap: 16px;
    font-size: 40px; font-weight: 700; letter-spacing: 2px;
    color: var(--navy); text-transform: uppercase;
  }
  .back-mark { width: 32px; height: 32px; background: var(--red); }
  .back-tagline {
    font-size: 13px; letter-spacing: 3px; color: var(--grey-text); text-transform: uppercase;
  }

  /* Front side */
  .front-band { position: absolute; inset: 0; width: 100%; height: 100%; }
  .front-content { position: absolute; left: 42px; top: 40px; color: var(--white); width: 300px; }
  .front-name {
    font-weight: 700; text-transform: uppercase; line-height: 1;
  }
  .front-name-main { display: block; font-size: 40px; letter-spacing: 2px; }
  .front-name-sub {
    display: flex; align-items: center; gap: 10px;
    margin-top: 6px; font-size: 15px; letter-spacing: 4px;
  }
  .front-name-sub::before, .front-name-sub::after {
    content: ""; flex: 1; height: 1px; background: rgba(255,255,255,.6);
  }
  .front-tagline {
    margin-top: 7px; font-size: 9.5px; letter-spacing: 1.6px; text-transform: uppercase;
    white-space: nowrap;
  }
  .person { margin-top: 16px; }
  .person-name { color: var(--red); font-size: 21px; }
  .person-role { font-size: 17px; margin-top: 2px; }
  .address { margin-top: 18px; font-size: 17px; line-height: 1.3; }
  .contacts { list-style: none; margin-top: 4px; font-size: 17px; line-height: 1.35; }
  .contacts li { display: flex; align-items: center; gap: 8px; }
  .contacts svg { width: 15px; height: 15px; fill: var(--red); flex: none; }
</style>
</head>
<body>

<section class="card card--back" aria-label="Business card, back">
  <div class="back-lockup">
    <div class="back-name"><span class="back-mark"></span>Brellwick Partners, LLC</div>
    <div class="back-tagline">Financial Planning and Consulting</div>
  </div>
</section>

<section class="card card--front" aria-label="Business card, front">
  <svg class="front-band" viewBox="0 0 760 434" preserveAspectRatio="none" aria-hidden="true">
    <polygon points="0,0 400,0 350,434 0,434" fill="var(--navy)"/>
    <polygon points="330,0 400,0 350,434 300,434" fill="var(--navy-deep)" opacity=".35"/>
  </svg>
  <div class="front-content">
    <div class="front-name">
      <span class="front-name-main">Brellwick</span>
      <span class="front-name-sub">Partners, LLC</span>
    </div>
    <div class="front-tagline">Financial Planning and Consulting</div>
    <div class="person">
      <div class="person-name">Marcus Hale</div>
      <div class="person-role">President</div>
    </div>
    <div class="address">2170 Linden Crest Road<br>Glen Harbor, NY 11020</div>
    <ul class="contacts">
      <li><svg viewBox="0 0 16 16"><path d="M3 1h3l1.5 4-2 1.2a9 9 0 0 0 4.3 4.3L11 8.5l4 1.5v3a2 2 0 0 1-2 2A12 12 0 0 1 1 3a2 2 0 0 1 2-2z"/></svg>555 0142 7781</li>
      <li><svg viewBox="0 0 16 16"><path d="M4 1h8v4H4zM1 6h14v6h-3v3H4v-3H1zm4 4v4h6v-4z"/></svg>555 0193 4620</li>
      <li><svg viewBox="0 0 16 16"><path d="M1 3h14v10H1zm1.5 1.2v.6L8 9l5.5-4.2v-.6z"/></svg>marcus@brellwick.com</li>
      <li><svg viewBox="0 0 16 16"><circle cx="8" cy="8" r="7"/></svg>www.brellwick.com</li>
    </ul>
  </div>
</section>

</body>
</html>
```